Flyer for the Lumen 2025 Conference

I am looking to produce a flyer for our upcoming conference, Lumen 2025. This is an annual conference that we plan to publicize on social media. The ideal designer will create a flyer that is eye-catching and effectively communicates the key information. Please see attached our logo, speaker photo, and flyer content.

Target Market(s)

All demographics

Industry/Entity Type

Christian

Font styles to use
Sans Serif

Requirements
Should not have
• Cross, church

```html
<!DOCTYPE html>
<html lang="en">
<head>
<meta charset="utf-8">
<title>Lumen 2025 Conference Flyer</title>
<link rel="stylesheet" href="https://fonts.googleapis.com/css2?family=Bebas+Neue&family=Oswald:wght@600&family=Barlow+Condensed:wght@300;400&display=swap">
<style>
  :root{
    --page:#a0a7b5;
    --navy-deep:#040a1f;
    --navy:#0a1433;
    --band:#0d1f57;
    --orange:#ff7a1a;
    --orange-light:#ffa733;
    --white:#ffffff;
    --royal:#1f4fb8;
  }
  *{margin:0;padding:0;box-sizing:border-box}
  html,body{width:1200px;height:1200px;overflow:hidden;background:var(--page)}
  .flyer{
    position:absolute;left:235px;top:128px;width:729px;height:943px;
    background:linear-gradient(180deg,var(--navy) 0%,var(--navy-deep) 32%);
    box-shadow:0 18px 40px rgba(20,25,40,.45);
    overflow:hidden;color:var(--white);
    font-family:"Bebas Neue",sans-serif;
  }
  .abs{position:absolute}
  .center{transform:translateX(-50%);text-align:center;white-space:nowrap}
  .brand{left:365px;top:62px;font-size:56px;line-height:1;letter-spacing:2px}
  .tagline{left:365px;top:113px;font-family:"Barlow Condensed",sans-serif;font-weight:400;font-size:13px;letter-spacing:1px;color:var(--orange)}
  .title{left:365px;top:133px;font-size:106px;line-height:1;letter-spacing:1px}
  .title .accent{background:linear-gradient(100deg,var(--orange) 0%,var(--orange-light) 50%,var(--orange) 100%);-webkit-background-clip:text;background-clip:text;color:transparent}
  .subtitle-box{left:170px;top:232px;width:388px;height:47px;background:var(--orange);
    font-family:"Oswald",sans-serif;font-weight:600;font-size:27px;letter-spacing:3.5px;
    display:flex;align-items:center;justify-content:center}
  .schedule-band{left:0;top:299px;width:729px;height:87px;background:var(--band)}
  .day-name{line-height:1;white-space:nowrap}
  .day-date{line-height:1;color:var(--orange);white-space:nowrap}
  .day-date .ord{font-size:10px;vertical-align:top;position:relative;top:2px;margin-left:1px}
  .time-box{top:314px;width:55px;height:58px;border:2px solid var(--orange);
    display:flex;flex-direction:column;align-items:center;justify-content:center;font-size:17px;line-height:1}
  .time-box .to{width:13px;height:13px;border-radius:50%;background:var(--orange);font-size:8px;line-height:13px;text-align:center;margin:1px 0}
  .scene{left:0;top:386px;width:729px;height:557px;
    background:radial-gradient(ellipse at 75% 45%,#1a2f6e 0%,#0d1a45 45%,var(--navy-deep) 85%)}
  .speaker-photo{left:0;top:400px;width:330px;height:543px;
    background:radial-gradient(ellipse at 45% 55%,var(--royal) 0%,#173a8a 40%,rgba(10,20,51,0) 78%)}
  .fade{left:0;top:780px;width:729px;height:163px;background:linear-gradient(180deg,rgba(4,10,31,0),var(--navy-deep) 70%)}
  .topic-label{left:365px;top:412px;font-size:26px;color:var(--orange)}
  .topic-1{left:365px;top:448px;font-size:44px;line-height:1}
  .topic-2{left:365px;top:482px;font-size:57px;line-height:1}
  .venue{left:365px;top:606px;font-family:"Barlow Condensed",sans-serif;font-weight:300;font-size:20px;line-height:25px}
  .address{left:365px;top:663px;font-family:"Barlow Condensed",sans-serif;font-weight:300;font-size:17px;line-height:21px}
  .app-title{left:531px;top:740px;font-size:25px;line-height:1}
  .app-title span{color:var(--orange)}
  .app-sub{left:531px;top:769px;font-size:17px;line-height:1}
  .store-badge{top:795px;width:104px;height:34px;border:1px solid #cfd4df;border-radius:5px;background:#000}
  .speaker-label{left:168px;top:834px;font-size:32px;line-height:1}
  .speaker-name{left:168px;top:866px;font-size:38px;line-height:1}
  .contact{font-family:"Barlow Condensed",sans-serif;font-weight:400;font-size:19px;line-height:1;display:flex;align-items:center;gap:8px}
</style>
</head>
<body>
<div class="flyer">
  <div class="abs scene" role="img" aria-label="Blurred photo of an auditorium audience in blue seats with a microphone on a stand"></div>
  <div class="abs speaker-photo" role="img" aria-label="Photo of the speaker seated, wearing a royal blue suit and glasses"></div>
  <div class="abs fade"></div>

  <div class="abs center brand">HALORA</div>
  <div class="abs center tagline">A LIGHT TO ALL PEOPLES</div>

  <h1 class="abs center title"><span class="accent">LUMEN</span> 2025</h1>
  <div class="abs subtitle-box">A PROPHETIC CONFERENCE</div>

  <div class="abs schedule-band"></div>

  <div class="abs day-name" style="left:83px;top:311px;font-size:49px">FRIDAY</div>
  <div class="abs day-date" style="left:83px;top:352px;font-size:23px">DECEMBER 26<span class="ord">TH</span></div>
  <div class="abs time-box" style="left:193px">6:30PM<div class="to">TO</div>9:00PM</div>

  <div class="abs day-name" style="left:279px;top:313px;font-size:38px">SATURDAY</div>
  <div class="abs day-date" style="left:278px;top:346px;font-size:25px">DECEMBER 27<span class="ord">TH</span></div>
  <div class="abs time-box" style="left:398px">5:30PM<div class="to">TO</div>8:00PM</div>

  <div class="abs day-name" style="left:481px;top:312px;font-size:44px">SUNDAY</div>
  <div class="abs day-date" style="left:481px;top:349px;font-size:22px">DECEMBER 29<span class="ord">TH</span></div>
  <div class="abs time-box" style="left:589px">4:30PM<div class="to">TO</div>7:00PM</div>

  <div class="abs center topic-label">TOPIC</div>
  <div class="abs center topic-1">THE VOICE OF</div>
  <div class="abs center topic-2">THE LORD</div>

  <svg class="abs" style="left:353px;top:568px" width="24" height="32" viewBox="0 0 24 32">
    <path d="M12 0C5.4 0 0 5.2 0 11.6 0 20 12 32 12 32s12-12 12-20.4C24 5.2 18.6 0 12 0z" fill="var(--orange)"/>
    <circle cx="12" cy="11.5" r="5" fill="var(--navy)"/>
  </svg>
  <div class="abs center venue">THE RIVERSIDE PERFORMING<br>ARTS CENTER</div>
  <div class="abs center address">218 MILLBROOK STREET<br>RIVERSIDE, MAINE 04100</div>

  <div class="abs center app-title">DOWNLOAD THE <span>HALORA APP</span></div>
  <div class="abs center app-sub">TO STAY UPDATED ON THE EVENT</div>
  <div class="abs store-badge" style="left:423px"></div>
  <div class="abs store-badge" style="left:535px"></div>

  <div class="abs contact" style="left:461px;top:856px;font-size:22px">
    <svg width="20" height="20" viewBox="0 0 24 24"><path d="M6.6 10.8a15.1 15.1 0 006.6 6.6l2.2-2.2a1 1 0 011-.25 11.4 11.4 0 003.6.57 1 1 0 011 1V20a1 1 0 01-1 1A17 17 0 013 4a1 1 0 011-1h3.5a1 1 0 011 1c0 1.25.2 2.45.57 3.6a1 1 0 01-.25 1z" fill="var(--orange)"/></svg>
    207 555 0142
  </div>
  <div class="abs contact" style="left:371px;top:882px">
    <svg width="24" height="16" viewBox="0 0 24 16"><rect x="1" y="1" width="22" height="14" fill="none" stroke="var(--orange)" stroke-width="2"/><path d="M1 1l11 8 11-8" fill="none" stroke="var(--orange)" stroke-width="2"/></svg>
    contact@halora.org
  </div>
  <div class="abs contact" style="left:557px;top:880px">
    <svg width="22" height="22" viewBox="0 0 24 24" fill="none" stroke="var(--orange)" stroke-width="1.8"><circle cx="12" cy="12" r="10.5"/><ellipse cx="12" cy="12" rx="4.5" ry="10.5"/><path d="M1.5 12h21M3.5 6.5h17M3.5 17.5h17"/></svg>
    www.halora.org
  </div>

  <div class="abs center speaker-label">SPEAKER</div>
  <div class="abs center speaker-name">PROPHET SAMUEL OKORO</div>
</div>
</body>
</html>
```